Sales/Landing Page Redesign for Hunting product

I am looking for a redesign for https://ridgelynoutfitters.com/quarter-pad .

We want to add in the information for our new XL quarterpad found: https://ridgelynoutfitters.com/shop/hunting/xl-big-game-quarter-pad/

We also will be adding a spot for this video: https://www.vidstreamhub.com/watch?v=Zk4TnaR8wqe

We like having the 3 options at the bottom, but the goal for this page is to sell the quarter pad.

Target Market(s)

Western Hunters, campers, outdoorsmen

Industry/Entity Type

Hunting

Number of Pages Required

1 page

Font styles to use
Sans Serif

Requirements
Must have
• a clean design that is geared to sell the product.

```html
<!DOCTYPE html>
<html lang="en">
<head>
<meta charset="utf-8">
<title>Ridgelyn Quarter Pads</title>
<link href="https://fonts.googleapis.com/css2?family=Roboto:wght@400;500;700;900&family=Noto+Serif:wght@400&display=swap" rel="stylesheet">
<style>
:root{
  --red:#e0141e;
  --ink:#1b1b1b;
  --muted:#555;
  --paper:#ffffff;
  --stone:#f4f2f1;
  --night:#232323;
  --footer:#1f1f1f;
  --line:#d9d9d9;
}
*{margin:0;padding:0;box-sizing:border-box}
html,body{width:1200px;height:3569px;overflow:hidden}
body{position:relative;font-family:"Roboto",sans-serif;color:var(--ink);background:var(--paper)}
.abs{position:absolute}
.btn{position:absolute;background:var(--red);color:#fff;font-weight:700;text-transform:uppercase;display:flex;align-items:center;justify-content:center;letter-spacing:.3px}
.photo{position:absolute}
.rule{position:absolute;height:2px;width:40px;background:#bbb}
.section-title{position:absolute;left:0;width:1200px;text-align:center;font-weight:700;font-size:21px;letter-spacing:.4px}

/* hero */
.hero{position:absolute;left:0;top:0;width:1200px;height:682px;overflow:hidden}
.hero .photo{inset:0;background:radial-gradient(ellipse at 35% 55%,#e0622a 0%,#c5521f 28%,#6c5a4c 55%,#4a4039 100%)}
.brand{position:absolute;color:#fff;font-weight:900;font-size:29px;letter-spacing:1px}
.nav a{position:absolute;top:29px;color:#fff;font-size:14px;font-weight:500;text-decoration:none;letter-spacing:.3px}
.nav a.active{text-decoration:underline;text-underline-offset:4px}
.cart{position:absolute;left:1126px;top:22px}
.cart-count{position:absolute;left:1152px;top:22px;width:15px;height:15px;border-radius:50%;background:var(--red);color:#fff;font-size:9px;font-weight:700;text-align:center;line-height:15px}
.hero h1{position:absolute;left:782px;top:208px;color:#fff;font-weight:900;font-size:47px;line-height:57px;letter-spacing:1px}
.btn-outline{border:2px solid #fff}
.dots{position:absolute;display:flex;gap:13px}
.dots span{width:9px;height:9px;border-radius:50%;background:#fff}
.dots span.ring{background:transparent;border:1.5px solid #fff}
.dots span.on{background:var(--red)}

/* products */
.card{position:absolute;top:808px;width:228px;height:367px;border:1px solid var(--line);background:#fff;text-align:center}
.card .bag{position:absolute;left:44px;top:30px;width:140px;height:165px;border-radius:30px 30px 14px 14px}
.card h3{position:absolute;left:0;width:100%;top:243px;font-size:13px;font-weight:700;letter-spacing:.2px}
.price{position:absolute;left:0;width:100%;top:270px;font-family:"Noto Serif",serif;color:var(--red);font-size:26px}
.price sup{font-size:13px;vertical-align:11px}
.card .btn{left:70px;top:315px;width:88px;height:27px;font-size:11px}

/* benefits */
.benefits{position:absolute;left:0;top:1224px;width:1200px;height:540px;overflow:hidden}
.benefits .photo{inset:0;background:linear-gradient(180deg,#7fb3e0 0%,#a9cde8 45%,#d7dfd6 75%,#8c6a45 100%)}
.benefits h2{position:absolute;left:582px;top:52px;font-size:22px;font-weight:700;letter-spacing:.3px}
.ticks{position:absolute;left:577px;top:108px;width:353px;list-style:none}
.ticks li{position:relative;padding:8px 0 8px 30px;font-size:15px;border-bottom:1px solid rgba(0,0,0,.18);line-height:19px}
.ticks li:last-child{border-bottom:none}
.ticks svg{position:absolute;left:9px;top:12px}

/* problems */
.problems{position:absolute;left:0;top:1764px;width:1200px;height:553px;background:var(--stone)}
.problems h2{position:absolute;left:130px;top:53px;font-size:21px;font-weight:700;letter-spacing:.4px}
.tile{position:absolute;background:#fff;display:flex;align-items:center;font-size:11.5px;line-height:15px;color:#333}
.tile.col{flex-direction:column;justify-content:center;text-align:center;gap:14px}
.tile.row{justify-content:center;gap:26px}

/* testimonials */
.reviews{position:absolute;left:0;top:2317px;width:1200px;height:483px;background:linear-gradient(180deg,#2a2a2a,#1c1c1c)}
.reviews .section-title{color:#fff;top:52px}
.quote{position:absolute;top:138px;width:298px;height:238px;border:3px solid #5a5a5a;color:#ddd;text-align:center}
.quote .mark{position:absolute;left:0;width:100%;top:26px;font-family:"Noto Serif",serif;font-size:34px;color:#fff;font-weight:700}
.quote p{position:absolute;left:32px;right:32px;top:79px;font-size:14.5px;line-height:19.5px}
.quote .bar{position:absolute;left:130px;top:165px;width:38px;height:1px;background:var(--red)}
.quote .who{position:absolute;left:0;width:100%;top:184px;font-size:13px;font-weight:700;color:#fff;letter-spacing:.3px}

/* guarantee */
.guarantee{position:absolute;left:0;top:2800px;width:1200px;height:438px;overflow:hidden}
.guarantee .photo{inset:0;background:linear-gradient(90deg,#f6f4f2 0%,#f6f4f2 42%,#c99d80 58%,#3a3130 75%,#e06a2a 100%)}
.guarantee h2{position:absolute;left:133px;top:62px;font-size:30px;font-weight:700;line-height:44px;letter-spacing:.5px}
.guarantee p{position:absolute;left:133px;top:172px;width:300px;font-size:16px;line-height:22.5px;color:#222}

/* footer */
.footer{position:absolute;left:0;top:3238px;width:1200px;height:331px;background:var(--footer);color:#ddd}
.footer h4{position:absolute;top:42px;font-size:13px;font-weight:700;color:#fff;letter-spacing:.3px}
.footer ul{position:absolute;top:84px;list-style:none;font-size:11.5px;line-height:20px;text-transform:uppercase;color:#ccc}
.social{position:absolute;left:965px;display:flex;align-items:center;gap:12px;font-size:11.5px;line-height:15px;color:#ccc}
.social i{width:24px;height:24px;border-radius:50%;background:#fff;display:block}
.footer .divider{position:absolute;left:133px;top:252px;width:934px;height:1px;background:#333}
.footer .copy{position:absolute;left:0;width:100%;top:286px;text-align:center;font-size:10px;color:#bbb}
</style>
</head>
<body>

<header class="hero">
  <div class="photo" role="img" aria-label="Harvested mule deer lying on an orange quarter pad on gravel ground"></div>
  <div class="brand" style="left:33px;top:22px">RIDGELYN</div>
  <nav class="nav">
    <a class="active" href="#" style="left:686px">HOME</a>
    <a href="#" style="left:765px">MEALS</a>
    <a href="#" style="left:847px">QUARTER PADS</a>
  </nav>
  <div class="btn" style="left:985px;top:22px;width:113px;height:31px;font-size:14px">Shop Now</div>
  <svg class="cart" width="32" height="30" viewBox="0 0 32 30" fill="none" stroke="#fff" stroke-width="2">
    <path d="M1 4h5l4 15h16l4-11H8"/><circle cx="12" cy="25" r="2.2"/><circle cx="24" cy="25" r="2.2"/>
  </svg>
  <div class="cart-count">0</div>
  <h1>QUARTER PADS<br>TO KEEP YOUR<br>MEAT CLEAN</h1>
  <div class="btn btn-outline" style="left:787px;top:402px;width:147px;height:47px;font-size:19px;font-weight:500">Buy Now</div>
  <div class="dots" style="left:550px;top:631px"><span></span><span></span><span class="ring"></span><span></span><span></span></div>
</header>

<section>
  <h2 class="section-title" style="top:727px">CHOOSE YOUR QUARTER PAD</h2>
  <div class="rule" style="left:580px;top:768px"></div>

  <div class="card" style="left:128px">
    <div class="bag" style="background:#c81d22" role="img" aria-label="Red quarter pad stuff sack with carabiner"></div>
    <h3>RED QUARTER PAD</h3>
    <div class="price">$19.<sup>99</sup></div>
    <div class="btn">Shop Now</div>
  </div>
  <div class="card" style="left:366px">
    <div class="bag" style="background:#f06a25" role="img" aria-label="Orange XL quarter pad stuff sack with carabiner"></div>
    <h3>XL BIG GAME QUARTER PAD</h3>
    <div class="price">$29.<sup>99</sup></div>
    <div class="btn">Shop Now</div>
  </div>
  <div class="card" style="left:604px">
    <div class="bag" style="background:#c81d22" role="img" aria-label="Quarter pad stuff sack with carabiner"></div>
    <h3>ORANGE QUARTER PAD</h3>
    <div class="price">$19.<sup>99</sup></div>
    <div class="btn">Shop Now</div>
  </div>
  <div class="card" style="left:843px">
    <div class="bag" style="background:#1f9a48" role="img" aria-label="Green quarter pad stuff sack with carabiner"></div>
    <h3>GREEN QUARTER PAD</h3>
    <div class="price">$19.<sup>99</sup></div>
    <div class="btn">Shop Now</div>
  </div>
</section>

<section class="benefits">
  <div class="photo" role="img" aria-label="Bowhunter with a pack walking across a rocky ridge under blue sky"></div>
  <h2>BE RESPONSIBLE. USE A QUARTER PAD.</h2>
  <ul class="ticks">
    <li><svg width="12" height="10" viewBox="0 0 12 10"><path d="M1 5l3.5 3.5L11 1.5" stroke="#e0141e" stroke-width="2.4" fill="none"/></svg>KEEP YOUR MEAT OFF THE DIRT</li>
    <li><svg width="12" height="10" viewBox="0 0 12 10"><path d="M1 5l3.5 3.5L11 1.5" stroke="#e0141e" stroke-width="2.4" fill="none"/></svg>LIGHTWEIGHT</li>
    <li><svg width="12" height="10" viewBox="0 0 12 10"><path d="M1 5l3.5 3.5L11 1.5" stroke="#e0141e" stroke-width="2.4" fill="none"/></svg>100% WATERPROOF</li>
    <li><svg width="12" height="10" viewBox="0 0 12 10"><path d="M1 5l3.5 3.5L11 1.5" stroke="#e0141e" stroke-width="2.4" fill="none"/></svg>REUSABLE</li>
    <li><svg width="12" height="10" viewBox="0 0 12 10"><path d="M1 5l3.5 3.5L11 1.5" stroke="#e0141e" stroke-width="2.4" fill="none"/></svg>55"X60" WHEN OPEN</li>
    <li><svg width="12" height="10" viewBox="0 0 12 10"><path d="M1 5l3.5 3.5L11 1.5" stroke="#e0141e" stroke-width="2.4" fill="none"/></svg>RESPECT THE ANIMAL BY KEEPING IT CONTAMINATION FREE.</li>
  </ul>
  <div class="btn" style="left:585px;top:362px;width:213px;height:36px;font-size:14px;font-weight:500">Select My Quarter Pad</div>
</section>

<section class="problems">
  <h2>DO YOU STILL...</h2>
  <div class="rule" style="left:131px;top:88px"></div>

  <div class="tile col" style="left:132px;top:131px;width:159px;height:141px">
    <svg width="44" height="40" viewBox="0 0 44 40"><ellipse cx="22" cy="20" rx="19" ry="17" fill="none" stroke="#e0141e" stroke-width="5"/><ellipse cx="20" cy="18" rx="7" ry="5" fill="#e0141e"/></svg>
    <span>LAY YOUR FRESH<br>MEAT ON A ROCK?</span>
  </div>
  <div class="tile col" style="left:301px;top:131px;width:159px;height:141px">
    <svg width="40" height="40" viewBox="0 0 40 40"><path d="M12 2h22a4 4 0 0 1 4 4v28a4 4 0 0 1-4 4H6a4 4 0 0 1-4-4V12z" fill="#e0141e"/></svg>
    <span>SEW BED SHEETS<br>TOGETHER?</span>
  </div>
  <div class="tile col" style="left:471px;top:131px;width:160px;height:141px">
    <svg width="50" height="42" viewBox="0 0 50 42"><path d="M25 4L4 40h42z" fill="#e0141e"/><path d="M25 22l-7 18h14z" fill="#fff"/><path d="M19 0l6 8 6-8" stroke="#e0141e" stroke-width="3" fill="none"/></svg>
    <span>USE A BLUE TARP?</span>
  </div>
  <div class="tile row" style="left:133px;top:283px;width:243px;height:143px">
    <svg width="48" height="36" viewBox="0 0 48 36" fill="none" stroke="#e0141e" stroke-width="3"><path d="M2 4c8-4 14 4 22 0s14 4 22 0v28c-8 4-14-4-22 0s-14-4-22 0z"/><path d="M2 14c8-4 14 4 22 0s14 4 22 0M2 23c8-4 14 4 22 0s14 4 22 0"/></svg>
    <span>LAY YOUR MEAT<br>IN THE DIRT?</span>
  </div>
  <div class="tile row" style="left:387px;top:283px;width:244px;height:143px">
    <svg width="46" height="46" viewBox="0 0 46 46" fill="none" stroke="#e0141e" stroke-width="3"><path d="M2 2h26v12h14v30H18V30H2z"/><path d="M18 14h10v16H18z"/></svg>
    <span>STUFF THE MEAT IN<br>OLD USED PILLOW<br>CASES?</span>
  </div>
  <div class="btn" style="left:133px;top:463px;width:222px;height:39px;font-size:14px;font-weight:500">Select My Quarter Pad</div>

  <div class="photo" style="left:657px;top:41px;width:410px;height:475px;background:linear-gradient(160deg,#9aa08a 0%,#6c6a5a 35%,#3f3d36 70%,#2c2a26 100%)" role="img" aria-label="Hunting backpack with an orange quarter pad tucked in the outer pocket"></div>
</section>

<section class="reviews">
  <h2 class="section-title">WHAT OTHERS ARE SAYING...</h2>
  <div class="rule" style="left:580px;top:92px;background:#888"></div>

  <div class="quote" style="left:132px">
    <div class="mark">“</div>
    <p>A must have for any hunter. Keeping meat clean from field to freezer, priceless!</p>
    <div class="bar"></div>
    <div class="who">CORBIN HASKELL</div>
  </div>
  <div class="quote" style="left:453px">
    <div class="mark">“</div>
    <p>This is something that is needed on every hunt! Light easy to carry and a necessity to keep your hard earned meat clean!</p>
    <div class="bar"></div>
    <div class="who">WADE PRUITT</div>
  </div>
  <div class="quote" style="left:769px">
    <div class="mark">“</div>
    <p>There is no better light weight option out there to keep your meat &amp; cape clean after a successful hunt.</p>
    <div class="bar"></div>
    <div class="who">DALTON REESE - @DREESE212</div>
  </div>

  <div class="dots" style="left:550px;top:425px"><span></span><span></span><span class="on"></span><span></span><span></span></div>
</section>

<section class="guarantee">
  <div class="photo" role="img" aria-label="Gloved hand unfolding a black and orange quarter pad outdoors"></div>
  <h2>100% QUALITY<br>GUARANTEE</h2>
  <p>We've designed our Quarter Pads for maximum performance and durability so you can keep the meat you harvest in the backcountry clean and out of the dirt. If you are at all unsatisfied, contact us and we'll make it right.</p>
  <div class="btn" style="left:133px;top:328px;width:130px;height:39px;font-size:14px;font-weight:500">Contact Us</div>
</section>

<footer class="footer">
  <div class="brand" style="left:159px;top:100px;font-size:30px">RIDGELYN</div>
  <h4 style="left:463px">MENU</h4>
  <ul style="left:463px">
    <li>Meals</li><li>Quarter Pads</li><li>Shop Now</li><li>Buy Orange Quarter Pad</li>
  </ul>
  <h4 style="left:699px">LINKS</h4>
  <ul style="left:699px">
    <li>My Account</li><li>Blog</li><li>Terms of Service Agreement</li><li>Refund and Return Policy</li><li>Privacy Policy Agreement</li>
  </ul>
  <h4 style="left:965px">FOLLOW US</h4>
  <div class="social" style="top:80px"><i></i><span>Like us on<br>CAMPFEED</span></div>
  <div class="social" style="top:131px"><i></i><span>Follow us on<br>CHIRPLINE</span></div>
  <div class="social" style="top:182px"><i></i><span>Follow us on<br>WORKNET</span></div>
  <div class="divider"></div>
  <div class="copy">Copyright © 2020 All Rights Reserved</div>
</footer>

</body>
</html>
```